Venture Capital Investment Firm

We are looking to overhaul our existing website (substantially), with only using the same logos (which we can provide).
We are an investment firm that focuses on making loans to late stage technology companies. Our site should ultimately look like other venture capital firms, and look modern and fresh. We have an existing website www.norvellhub.com which this will be replacing, although we will be using a lot of the existing written content, and potentially the numbers of pages we will need, we are not wed to anything else. Please feel free to shoot any questions at any time and thank you in advance for your help!
Websites we like as examples:
https://www.tesmarkfund.com/
https://www.brindlewoodpartners.com/
Target Market(s)
Potential investors who will invest in our firm, as well as potentially companies that are looking to borrow money from us.
Coding
Coded - Design and coding required
Number of Pages Required
5+ page
Colors
Designer to choose colors to be used in the design.
Look and feel

```html
<!DOCTYPE html>
<html lang="en">
<head>
<meta charset="utf-8">
<title>Corvane Capital Partners</title>
<link href="https://fonts.googleapis.com/css2?family=Cinzel:wght@600;700&family=Oswald:wght@300;500&family=Montserrat:wght@400;500&display=swap" rel="stylesheet">
<style>
:root{
  --navy:#06066e;
  --royal:#1a1a9e;
  --footer:#0a0a85;
  --ink:#0a0a5c;
  --grey-bg:#f4f4f4;
  --card:#f3f3f3;
  --text:#6a6a7a;
  --white:#ffffff;
  --serif:'Cinzel', Georgia, serif;
  --cond:'Oswald', 'Arial Narrow', sans-serif;
  --sans:'Montserrat', Arial, sans-serif;
}
*{box-sizing:border-box;margin:0;padding:0}
html,body{width:1200px;height:3495px;overflow:hidden}
body{position:relative;font-family:var(--sans);color:var(--text);background:var(--white)}
.abs{position:absolute}
.btn{position:absolute;display:flex;align-items:center;justify-content:center;border-radius:26px;font-family:var(--serif);font-weight:700;font-size:19px;letter-spacing:.5px;text-decoration:none}
.btn-light{background:var(--white);color:var(--ink)}
.btn-dark{background:var(--ink);color:var(--white)}

/* hero */
.hero{position:absolute;left:0;top:0;width:1200px;height:675px;background:#1a1aa0}
.hero-photo{position:absolute;inset:0;
  background:
    radial-gradient(ellipse 260px 300px at 880px 360px,rgba(150,185,245,.85) 0%,rgba(90,120,225,.6) 40%,rgba(40,40,170,0) 100%),
    radial-gradient(ellipse 420px 520px at 900px 330px,rgba(60,80,200,.7) 0%,rgba(30,30,160,0) 100%),
    linear-gradient(90deg,#1d1da6 0%,#1b1ba2 45%,#2020ac 70%,#12128a 100%)}
.brand{position:absolute;display:flex;align-items:center;gap:10px;font-family:var(--serif);font-weight:600;color:var(--white)}
.brand .dot{width:14px;height:14px;border-radius:50%;background:var(--white)}
.nav{position:absolute;right:81px;top:30px;display:flex;gap:26px;font-size:15px;color:var(--white);letter-spacing:.3px}
.hero h1{position:absolute;left:79px;top:236px;font-family:var(--cond);font-weight:500;font-size:40px;line-height:47px;color:var(--white);text-transform:uppercase;letter-spacing:.3px}
.hero .sub{position:absolute;left:79px;top:385px;font-family:var(--cond);font-weight:300;font-size:19px;color:var(--white);text-transform:uppercase}

/* idea */
.idea-img{left:77px;top:785px;width:468px;height:538px;
  background:
    radial-gradient(ellipse 150px 110px at 240px 200px,rgba(120,170,255,.95) 0%,rgba(40,80,255,.75) 45%,rgba(20,40,220,0) 100%),
    radial-gradient(ellipse 60px 70px at 240px 390px,rgba(60,110,255,.9) 0%,rgba(20,40,220,0) 100%),
    radial-gradient(ellipse 260px 300px at 234px 260px,#1230d8 0%,#0a1890 40%,#050a4a 75%,#030630 100%)}
.idea h2{position:absolute;left:602px;top:772px;font-family:var(--serif);font-weight:700;font-size:41px;line-height:47px;color:var(--ink);letter-spacing:.5px}
.idea .tag{position:absolute;left:602px;top:872px;font-size:16px;line-height:23px;color:#222;text-transform:uppercase;width:400px}
.idea p{position:absolute;left:602px;top:940px;width:410px;font-size:14.5px;line-height:27px;color:var(--text)}
.idea .label{position:absolute;left:602px;top:1091px;font-size:16px;color:var(--ink);font-weight:500}
.stat{position:absolute;top:1126px;width:170px;text-align:center}
.stat b{display:block;font-family:var(--serif);font-weight:700;font-size:40px;color:var(--ink);line-height:48px}
.stat span{display:block;font-size:14px;line-height:27px;color:var(--text)}

/* testimonials */
.testi{position:absolute;left:0;top:1431px;width:1200px;height:474px;background:var(--grey-bg)}
.sec-title{position:absolute;left:0;width:1200px;text-align:center;font-family:var(--serif);font-weight:700;font-size:41px;letter-spacing:.5px}
.avatar{position:absolute;left:76px;top:171px;width:158px;height:158px;border-radius:50%;border:3px solid var(--ink);background:linear-gradient(160deg,#c98a6a,#7a4a3a)}
.quote{position:absolute;left:281px;top:174px;width:830px;font-size:14.5px;line-height:27px;color:var(--text)}
.who{position:absolute;left:281px;top:276px;font-family:var(--serif);font-weight:700;font-size:21px;color:var(--ink)}
.dots{position:absolute;left:529px;top:378px;display:flex;gap:15px}
.dots i{width:16px;height:16px;border-radius:50%;border:2px solid var(--ink)}
.dots i.on{background:var(--ink)}

/* team */
.team{position:absolute;left:0;top:1905px;width:1200px;height:609px;background:var(--navy)}
.member{position:absolute;top:125px;width:323px;height:312px;overflow:hidden}
.member .photo{position:absolute;inset:0;
  background:
    radial-gradient(ellipse 70px 85px at 50% 30%,#9a9a9a 0%,#bdbdbd 60%,rgba(240,240,240,0) 100%),
    linear-gradient(180deg,#f3f3f3 0%,#ececec 45%,#8a8a8a 62%,#2e2e2e 75%,#1c1c1c 100%)}
.member .band{position:absolute;left:0;bottom:0;width:100%;height:81px;background:rgba(32,32,150,.88);text-align:center;color:var(--white)}
.member h3{font-family:var(--serif);font-weight:700;font-size:21px;margin-top:14px;letter-spacing:.5px}
.member small{display:block;font-size:14px;margin-top:2px}

/* news */
.news-card{position:absolute;top:2693px;width:323px;background:var(--card);padding:20px 20px 0}
.news-card h4{font-size:16px;line-height:23px;font-weight:500;color:var(--ink)}
.news-card .date{font-family:Georgia,serif;font-size:15px;color:#999;margin-top:10px;letter-spacing:.5px}
.news-card p{font-size:14px;line-height:27px;color:var(--text);margin-top:18px}
.news-card a{display:inline-block;margin-top:20px;font-family:var(--serif);font-weight:700;font-size:17px;color:var(--ink);text-decoration:underline}

/* footer */
.footer{position:absolute;left:0;top:3086px;width:1200px;height:345px;background:var(--footer);color:var(--white)}
.footer h5{position:absolute;font-family:var(--serif);font-weight:700;font-size:19px;letter-spacing:.5px}
.fline{position:absolute;font-size:14.5px;line-height:23px;color:#dfe0ff}
.field{position:absolute;left:791px;width:323px;height:46px;border:1px solid rgba(255,255,255,.25);background:rgba(255,255,255,.04);font-size:14.5px;color:#dfe0ff;padding:13px 15px}
.legal{position:absolute;top:200px;left:175px;font-size:15px;color:#dfe0ff;text-decoration:underline}
.copy{position:absolute;left:0;top:3431px;width:1200px;height:64px;background:#f0f0f0;text-align:center;line-height:64px;font-size:14px;color:var(--ink)}
</style>
</head>
<body>

<header class="hero">
  <div class="hero-photo" role="img" aria-label="Glass skyscrapers photographed from below, tinted royal blue"></div>
  <div class="brand" style="left:77px;top:24px;font-size:26px"><span class="dot"></span>Corvane Capital</div>
  <nav class="nav">
    <span>HOME</span><span>STRATEGY</span><span>ABOUT US</span><span>TEAM</span><span>NEWS</span><span>CONTACT</span><span>INVESTORS</span>
  </nav>
  <h1>We are a global structured<br>credit investment firm<br>focused on the</h1>
  <div class="sub">Healthcare and technology industries</div>
  <a class="btn btn-light" style="left:77px;top:441px;width:187px;height:52px">LEARN MORE</a>
</header>

<section class="idea">
  <div class="abs idea-img" role="img" aria-label="Glowing blue light bulb containing a brain"></div>
  <h2>CORVANE STARTED<br>WITH A BIG IDEA</h2>
  <div class="tag">Finance proven innovation with a different approach</div>
  <p>Corvane Capital is a private investment firm unique in its dual focus on life science and technology credit opportunities. Our ambidextrous approach to investing reflects a broad recognition and appreciation for.</p>
  <div class="label">OUR EXPERIENCE</div>
  <div class="stat" style="left:601px"><b>$1.2B</b><span>Over $1.2B invested<br>by our partners</span></div>
  <div class="stat" style="left:776px"><b>40+</b><span>40 Life science and<br>technology<br>investments</span></div>
  <div class="stat" style="left:951px"><b>12+</b><span>Over a decade<br>innovating financing<br>structures</span></div>
  <a class="btn btn-dark" style="left:601px;top:1272px;width:182px;height:52px">LEARN MORE</a>
</section>

<section class="testi">
  <h2 class="sec-title" style="top:70px;color:var(--ink)">WHAT OUR PARTNERS SAY</h2>
  <div class="avatar" role="img" aria-label="Portrait photo of a partner"></div>
  <p class="quote">Lorem Ipsum is simply dummy text of the printing and typesetting industry. Lorem Ipsum has been the industry's standard dummy text ever since the 1500s, when an unknown printer took a galley of type and scrambled it to make a type specimen book.</p>
  <div class="who">CEO - PARTNER NAME</div>
  <div class="dots"><i class="on"></i><i></i><i></i><i></i><i></i></div>
</section>

<section class="team">
  <h2 class="sec-title" style="top:55px;color:var(--white)">MEET OUR TEAM</h2>
  <div class="member" style="left:77px"><div class="photo" role="img" aria-label="Black and white portrait of a partner in a dark suit"></div><div class="band"><h3>MARCUS ELLERY</h3><small>Managing Partner</small></div></div>
  <div class="member" style="left:438px"><div class="photo" role="img" aria-label="Black and white portrait of a partner in a dark suit"></div><div class="band"><h3>DANIEL OKAFOR</h3><small>Managing Partner</small></div></div>
  <div class="member" style="left:800px"><div class="photo" role="img" aria-label="Black and white portrait of a partner in a dark suit"></div><div class="band"><h3>PETER HOLLIS</h3><small>Partner</small></div></div>
  <a class="btn btn-light" style="left:436px;top:469px;width:328px;height:52px">KNOW MORE ABOUT TEAM</a>
</section>

<section class="news">
  <h2 class="sec-title" style="top:2600px;color:var(--ink)">CORVANE NEWS</h2>
  <article class="news-card" style="left:77px;height:277px">
    <h4>Corvane Capital completes structured debt investment in Learnwell</h4>
    <div class="date">APRIL 30, 2018</div>
    <p>Corvane Capital Partners ("Corvane") announced today that it has completed a structured...</p>
    <a>READ MORE</a>
  </article>
  <article class="news-card" style="left:438px;height:301px">
    <h4>Corvane Capital completes $22,000,000 structured debt investment in Surveyora</h4>
    <div class="date">OCTOBER 19, 2016</div>
    <p>Corvane Capital Partners ("Corvane") announced today that it has completed a $22,000,000...</p>
    <a>READ MORE</a>
  </article>
  <article class="news-card" style="left:800px;height:277px">
    <h4>Brightcore Semiconductor acquired by Lumatek for $55,000,000</h4>
    <div class="date">APRIL 4, 2016</div>
    <p>Lumatek, Inc., a leading supplier of advanced semiconductor communications components for...</p>
    <a>READ MORE</a>
  </article>
</section>

<footer class="footer">
  <div class="brand" style="left:98px;top:140px;font-size:30px"><span class="dot" style="width:16px;height:16px"></span>Corvane Capital</div>
  <span class="legal">Legal Disclaimer</span>

  <h5 style="left:435px;top:34px">CONTACT US</h5>
  <svg class="abs" style="left:432px;top:81px" width="20" height="28" viewBox="0 0 20 28" aria-hidden="true"><path d="M10 0C4.5 0 0 4.4 0 9.8 0 17 10 28 10 28s10-11 10-18.2C20 4.4 15.5 0 10 0zm0 14a4 4 0 1 1 0-8 4 4 0 0 1 0 8z" fill="#fff"/></svg>
  <div class="fline" style="left:484px;top:80px">SAN FRANCISCO<br>1450 Alder Street #318<br>San Francisco, CA&nbsp; 94107</div>
  <svg class="abs" style="left:432px;top:186px" width="23" height="17" viewBox="0 0 23 17" aria-hidden="true"><rect width="23" height="17" rx="2" fill="#fff"/><path d="M1 2l10.5 8L22 2" stroke="#0a0a85" stroke-width="2" fill="none"/></svg>
  <div class="fline" style="left:484px;top:180px">GENERAL INQUIRIES :<br>inquiries@corvanecap.com</div>
  <svg class="abs" style="left:432px;top:256px" width="23" height="17" viewBox="0 0 23 17" aria-hidden="true"><rect width="23" height="17" rx="2" fill="#fff"/><path d="M1 2l10.5 8L22 2" stroke="#0a0a85" stroke-width="2" fill="none"/></svg>
  <div class="fline" style="left:484px;top:250px">MEDIA INQUIRIES :<br>media@corvanecap.com</div>

  <h5 style="left:793px;top:34px">NEWSLETTER</h5>
  <div class="fline" style="left:793px;top:80px;width:330px;line-height:27px">Would you like to receive our exclusive news and update for signup our newsletter !</div>
  <div class="field" style="top:141px">Enter Name *</div>
  <div class="field" style="top:196px">Enter Email *</div>
  <a class="btn btn-light" style="left:791px;top:252px;width:160px;height:52px">SUBSCRIBE</a>
</footer>

<div class="copy">©2019 Corvane Capital Partners LLC.&nbsp; All Rights Reserved.</div>

</body>
</html>
```